Inspirational Quotes Poster Set

Brookloft is a stylish coworking space, which has a design-oriented vintage look from the 60's with an industrial touch (www.brookloft-example.com) Brookloft Quote Poster Set of 16 posters. The poster should be typo oriented and rather simple. Reflecting a bit the clean billboard design from the sixties. Minimal / simple graphical elements

Target Market(s)

Startups and Entrepreneurs

Industry/Entity Type

Startup

Font styles to use
Sans Serif

Colors

Designer to choose colors to be used in the design.

Requirements
Must have
• Posters need to be on and very stylish

```html
<!DOCTYPE html>
<html lang="en">
<head>
<meta charset="utf-8">
<title>Brookloft Quote Poster Set – Never Give Up</title>
<link rel="stylesheet" href="https://fonts.googleapis.com/css2?family=Arimo:wght@400;700&display=swap">
<style>
  :root {
    --canvas-bg: #e9e6e2;
    --poster-orange: #e9501b;
    --never-deep: #4e1700;
    --never-rust: #722800;
    --muted-grey: #8a8a8a;
    --paper-white: #ffffff;
  }
  html, body {
    margin: 0;
    padding: 0;
    width: 1200px;
    height: 1200px;
    overflow: hidden;
    background: var(--canvas-bg);
  }
  .poster {
    position: absolute;
    left: 160px;
    top: 5px;
    width: 880px;
    height: 1190px;
    display: block;
  }
  .poster-bg { fill: var(--poster-orange); }
  .headline {
    font-family: "Arimo", Helvetica, Arial, sans-serif;
    font-weight: 700;
    font-size: 251px;
    letter-spacing: -17px;
  }
  .headline--deep { fill: var(--never-deep); }
  .headline--rust { fill: var(--never-rust); }
  .underline-bar { fill: var(--never-rust); }
  .tagline {
    font-family: "Arimo", Helvetica, Arial, sans-serif;
    font-weight: 700;
    font-size: 74px;
    fill: var(--muted-grey);
  }
  .attribution {
    font-family: "Arimo", Helvetica, Arial, sans-serif;
    font-weight: 700;
    font-size: 24px;
    fill: var(--paper-white);
  }
  .brand-name {
    font-family: "Arimo", Helvetica, Arial, sans-serif;
    font-weight: 700;
    font-size: 60px;
    letter-spacing: -2px;
    fill: var(--paper-white);
  }
</style>
</head>
<body>
  <svg class="poster" viewBox="0 0 880 1190" xmlns="http://www.w3.org/2000/svg" aria-label="Quote poster: Never never never give up">
    <defs>
      <clipPath id="poster-edge">
        <rect x="0" y="0" width="880" height="1190"/>
      </clipPath>
    </defs>
    <g clip-path="url(#poster-edge)">
      <rect class="poster-bg" x="0" y="0" width="880" height="1190"/>

      <text class="headline headline--deep" x="-4" y="291">NEVER</text>
      <text class="headline headline--deep" x="50" y="498">NEVER</text>
      <text class="headline headline--rust" x="107" y="704">NEVER</text>

      <rect class="underline-bar" x="109" y="725" width="771" height="30"/>
      <text class="tagline" x="141" y="758">give up.</text>

      <text class="attribution" x="64" y="945">WILFRED HARCOURT,</text>
      <text class="attribution" x="64" y="975">BRITISH PRIME MINISTER</text>

      <text class="brand-name" x="836" y="1130" text-anchor="end">brookloft</text>
    </g>
  </svg>
</body>
</html>
```